Business card design

I already have the logo design completed and am requiring business card design and layout utilising the logo. I require a front and back design.

We are an executive recruitment company so we are looking at full colour, high finish in a reasonably conservative structure.

Reason: will be provide ai template

Target Market(s)

Senior Management 35-60 age bracket

Industry/Entity Type

Business

Requirements
Must have
• Peter Welling
• Director
• 238 Morrow Tce, Kelvin Grove QLD 4059
• Ph: 07 3628 4190 Mob: 0418527306
• peter@voltinapartners.com.au
• www.voltinapartners.com.au
Nice to have
• Ideally full colour,
Should not have
• cheap looking

```html
<!DOCTYPE html>
<html lang="en">
<head>
<meta charset="utf-8">
<title>Voltina Partners – Business Card</title>
<link href="https://fonts.googleapis.com/css2?family=Open+Sans:wght@400;600;700&display=swap" rel="stylesheet">
<style>
  :root {
    --navy: #123f70;
    --navy-deep: #0c2d58;
    --blue-mid: #1d4f8c;
    --grey-text: #8a8a8a;
    --grey-dark: #555555;
    --band: #a0a0a0;
    --paper: #ffffff;
    --page: #f2f2f2;
  }
  * { margin: 0; padding: 0; box-sizing: border-box; }
  html, body { width: 900px; height: 1200px; overflow: hidden; }
  body {
    position: relative;
    background: var(--page);
    font-family: "Open Sans", Arial, sans-serif;
  }
  .brand-header {
    position: absolute; left: 0; top: 0; width: 900px; height: 222px;
    background: var(--paper);
    display: flex; align-items: center; justify-content: center;
  }
  .brand-name {
    font-weight: 700; color: var(--navy);
    letter-spacing: 1px; text-transform: uppercase; white-space: nowrap;
    display: flex; align-items: center; gap: 12px;
  }
  .brand-mark {
    display: inline-block; background: currentColor;
  }
  .brand-header .brand-name { font-size: 40px; }
  .brand-header .brand-mark { width: 34px; height: 34px; }

  .card-band {
    position: absolute; left: 0; top: 222px; width: 900px; height: 292px;
    background: var(--band);
  }
  .card {
    position: absolute; top: 44px; width: 378px; height: 210px;
  }
  .card-front {
    left: 50px; background: var(--paper);
    border-right: 6px solid var(--navy);
  }
  .card-front .brand-name {
    position: absolute; left: 31px; top: 28px; font-size: 20px; gap: 8px;
  }
  .card-front .brand-mark { width: 18px; height: 18px; }
  .person {
    position: absolute; left: 29px; top: 112px;
  }
  .person-name { font-size: 14.5px; font-weight: 700; color: var(--navy); line-height: 18px; }
  .person-role { font-size: 12px; color: var(--grey-dark); letter-spacing: 0.5px; line-height: 16px; }
  .contact {
    position: absolute; left: 190px; top: 110px;
    font-size: 10.5px; line-height: 16.3px; color: var(--grey-text); list-style: none;
  }

  .card-back {
    left: 475px;
    background: linear-gradient(180deg, var(--blue-mid) 0%, var(--navy-deep) 100%);
    border-right: 7px solid #7d7d7d;
  }
  .card-back .brand-name {
    position: absolute; left: 0; right: 0; top: 86px; justify-content: center;
    color: #ffffff; font-size: 21px; gap: 8px;
  }
  .card-back .brand-mark { width: 18px; height: 18px; }
  .web {
    position: absolute; left: 0; right: 0; bottom: 10px;
    text-align: center; color: #ffffff; font-size: 12.5px; font-weight: 600; letter-spacing: 0.3px;
  }
</style>
</head>
<body>
  <header class="brand-header">
    <div class="brand-name"><span class="brand-mark"></span>Voltina Partners</div>
  </header>

  <section class="card-band">
    <article class="card card-front">
      <div class="brand-name"><span class="brand-mark"></span>Voltina Partners</div>
      <div class="person">
        <p class="person-name">Peter Welling</p>
        <p class="person-role">Director</p>
      </div>
      <ul class="contact">
        <li>238 Morrow Tce,</li>
        <li>Kelvin Grove QLD 4059</li>
        <li>P&nbsp;&nbsp;: 07 3628 4190</li>
        <li>M : 0418 527 306</li>
        <li>peter@voltinapartners.com.au</li>
      </ul>
    </article>

    <article class="card card-back">
      <div class="brand-name"><span class="brand-mark"></span>Voltina Partners</div>
      <p class="web">www.voltinapartners.com.au</p>
    </article>
  </section>
</body>
</html>
```